Personal website for my flying adventures

It is the website for my personal flying adventures.

1. I flew around the world in 2011 and became the first Chinese citizen ever flying the single engine airplane around the world in the history and also the first ever to land the single engine airplane in Halvern Ridge airport.
2. I am organizing the "Copper Kestrels Aerobatic Flying Team" in China
3. I am sharing my flying experiences regularly
4. I am writing the book about flying around the world.

Visit: www.lutanmo.com and www.tanmoskyloop.com for more information and pictures on my flying activities. Need connect two websites together well.

Target Market(s)

Young pilots

Industry/Entity Type

Airport

Requirements
Must have
• Must have the logo of "Tanmo Sky Loop"
• Must have the logo of "Copper Kestrels"
• Must have my flying pictures

```html
<!DOCTYPE html>
<html lang="en">
<head>
<meta charset="utf-8">
<title>Tanmo Sky Loop</title>
<link href="https://fonts.googleapis.com/css2?family=Roboto+Condensed:wght@400;700&family=PT+Sans+Narrow:wght@400;700&display=swap" rel="stylesheet">
<style>
:root{
  --red:#d8262d;
  --navy:#05083a;
  --ink:#222;
  --grey:#666;
  --cream:#ede3d6;
  --footer:#3a3a3a;
  --line:#dcdcdc;
  --sponsor:#1a5fb4;
}
*{margin:0;padding:0;box-sizing:border-box}
html,body{width:1200px;height:1136px;overflow:hidden;background:#fff}
body{position:relative;font-family:"PT Sans Narrow",sans-serif;color:var(--ink)}
.head{position:absolute;left:0;top:0;width:1200px;height:73px;background:#fff}
.logo-bubble{position:absolute;left:183px;top:0;width:180px;height:133px;background:#fff;border-radius:0 0 90px 90px;z-index:3;display:flex;flex-direction:column;align-items:center;justify-content:center;gap:6px}
.logo-mark{width:78px;height:78px;border-radius:50%;background:#1e9ad6}
.logo-name{font-family:"Roboto Condensed",sans-serif;font-weight:700;font-size:11px;color:var(--red)}
.lang{position:absolute;left:650px;top:25px;font-size:11px;color:var(--grey);display:flex;align-items:center;gap:6px}
.lang-box{border:1px solid #bbb;border-radius:3px;padding:3px 8px;display:flex;align-items:center;gap:6px;color:#333;background:linear-gradient(#fff,#eee)}
.flag{width:16px;height:10px;background:#2a3c8c}
.topnav{position:absolute;right:180px;top:30px;display:flex;gap:20px;font-size:10px;color:#444}
.hero{position:absolute;left:0;top:73px;width:1200px;height:501px;background:linear-gradient(180deg,#8d7a66 0%,#c88a4d 30%,#e88a3a 50%,#6a4a3a 72%,#3a2e2c 100%)}
.mainnav{position:absolute;left:474px;top:93px;display:flex;z-index:2}
.mainnav a{color:#fff;text-decoration:none;font-size:14px;width:153px}
.hero-badge{position:absolute;left:726px;top:184px;width:288px;height:288px;border-radius:50%;background:rgba(100,82,66,.88);text-align:center;color:var(--cream)}
.hero-badge .big{font-family:"Roboto Condensed",sans-serif;font-weight:700;font-size:62px;line-height:1;margin-top:56px}
.hero-badge .sub{font-family:"Roboto Condensed",sans-serif;font-size:27px;margin-top:4px}
.hero-badge hr{border:0;border-top:1px solid rgba(237,227,214,.4);width:230px;margin:10px auto 12px}
.hero-badge p{font-size:9.5px;line-height:19px;width:220px;margin:0 auto;color:#fff}
.dots{position:absolute;right:180px;top:551px;display:flex;gap:3px}
.dots i{width:11px;height:11px;border-radius:50%;background:rgba(255,255,255,.7)}
.sponsors{position:absolute;left:0;top:574px;width:1200px;height:143px;border-bottom:2px solid var(--line)}
.sponsors h2{position:absolute;left:182px;top:21px;font-weight:400;font-size:17px;color:var(--red)}
.sponsors .lead{position:absolute;left:182px;top:45px;font-size:11px;color:#111}
.arrows{position:absolute;left:988px;top:41px;display:flex;gap:3px}
.arrows span{width:14px;height:14px;background:#bbb}
.sponsor-row{position:absolute;left:182px;top:80px;width:838px;height:56px;display:flex;align-items:center;justify-content:space-between;font-weight:700;font-size:16px;color:var(--sponsor)}
.sponsor-row .dot{display:inline-block;width:34px;height:34px;border-radius:50%;background:#e04a2a}
.welcome{position:absolute;left:180px;top:743px;width:840px;height:192px;background:var(--navy);border-left:11px solid var(--red)}
.welcome-photo{position:absolute;left:0;top:0;width:395px;height:192px;background:linear-gradient(90deg,#1b3a6b,#0b1848 80%,var(--navy))}
.welcome-text{position:absolute;left:405px;top:18px;width:410px;color:#fff}
.welcome-text .pre{font-family:"Roboto Condensed",sans-serif;font-size:20px}
.welcome-text h1{font-family:"Roboto Condensed",sans-serif;font-weight:700;font-size:34px;line-height:1.1;margin-bottom:8px}
.welcome-text p{font-size:10px;line-height:15.5px}
.pilot{position:absolute;left:180px;top:962px;width:840px;height:70px}
.pilot h2{font-family:"Roboto Condensed",sans-serif;font-weight:400;font-size:25px;color:#444}
.btn{display:inline-block;margin-top:6px;background:var(--red);color:#fff;font-size:10px;width:81px;height:20px;line-height:20px;text-align:center}
.pilot .rule{position:absolute;left:115px;top:3px;height:58px;border-left:1px solid #ccc}
.pilot p{position:absolute;left:132px;top:4px;width:708px;font-size:9.5px;line-height:15.5px;color:#333}
.pilot strong{font-weight:700;color:var(--red)}
.foot{position:absolute;left:0;top:1047px;width:1200px;height:89px;background:var(--footer);color:#ddd}
.foot .pdf{position:absolute;left:185px;top:14px;width:64px;height:64px;border-radius:50%;background:radial-gradient(circle at 40% 35%,#f05050,#a3141a)}
.foot .itin{position:absolute;left:260px;top:20px;font-family:"Roboto Condensed",sans-serif;color:#ccc}
.foot .itin b{display:block;font-weight:400;font-size:22px}
.foot .itin span{font-size:13px}
.foot .sep{position:absolute;left:468px;top:13px;height:58px;border-left:1px solid #666}
.foot nav{position:absolute;left:488px;top:29px;font-size:8.5px;display:flex;gap:11px}
.foot .copy{position:absolute;left:488px;top:46px;font-size:8px}
.social{position:absolute;left:945px;top:32px;display:flex;gap:4px}
.social span{width:22px;height:22px;border-radius:4px;background:#8a8a8a}
</style>
</head>
<body>
<header class="head">
  <div class="logo-bubble"><div class="logo-mark"></div><div class="logo-name">www.lutanmo.com</div></div>
  <div class="lang">Select Language : <span class="lang-box"><span class="flag"></span>English ▾</span></div>
  <nav class="topnav"><span>HOME</span><span>|</span><span>CONTESTS</span><span>|</span><span>STORE</span></nav>
</header>
<section class="hero" role="img" aria-label="Private jet parked on a wet runway at sunset"></section>
<nav class="mainnav"><a>THE EXPEDITION</a><a>MEDIA ROOM</a><a>SPONSORS</a><a>TANMO TRACKER</a></nav>
<div class="hero-badge">
  <div class="big">TANMO</div>
  <div class="sub">SKY LOOP</div>
  <hr>
  <p>WELCOME TO THE ONLINE MEDIA ROOM FOR THE TANMO SKY LOOP WHERE YOU CAN FIND PRESS RELEASES AND OTHER NEWS</p>
</div>
<div class="dots"><i></i><i></i><i></i></div>
<section class="sponsors">
  <h2>SPONCERS</h2>
  <p class="lead">GLOBAL SPONSORSHIP OPPORTUNITIES AVAILABLE INTENDED TO TOUCH THE HEARTS AND MINDS OF OVER 1.3 BILLION CHINESE.</p>
  <div class="arrows"><span></span><span></span></div>
  <div class="sponsor-row">
    <span class="dot"></span><span>Lantern Net</span><span>Harbor Daily</span><span>Ripple Post</span><span>Aeromax Parts</span><span>The Westbrook Hotel</span><span>Riverbend Chamber</span>
  </div>
</section>
<section class="welcome">
  <div class="welcome-photo" role="img" aria-label="White business jet flying above the ocean"></div>
  <div class="welcome-text">
    <div class="pre">Welcome to</div>
    <h1>TANMO SKY LOOP</h1>
    <p>The first round-the-world flight in a single engine airplane took place in 1919. Pilots from 28 countries had achieved the challenge, but never a Chinese citizen. In 2011, Lu Tanmo flew his single engine plane around the world, becoming the first Chinese citizen ever to do so and the first pilot ever to land a single engine airplane at Halvern Ridge airport.</p>
  </div>
</section>
<section class="pilot">
  <h2>THE PILOT</h2>
  <span class="btn">READ MORE</span>
  <span class="rule"></span>
  <p>Lu Tanmo was born in Changsha City, Hunan province of People's Republic of China in 1971. He earned his MBA from the University of Larkmoor in 1998 and founded Brightfield Enterprise, Inc. in 1999. Today he is organizing the <strong>Copper Kestrels Aerobatic Flying Team</strong> in China, shares his flying experiences regularly and is writing a book about his flight around the world. More stories and pictures at www.lutanmo.com and www.tanmoskyloop.com.</p>
</section>
<footer class="foot">
  <div class="pdf"></div>
  <div class="itin"><b>FLIGHT ITINERARY</b><span>DOWNLOAD LATEST FLIGHT ITINERARY</span></div>
  <span class="sep"></span>
  <nav><span>HOME</span><span>|</span><span>THE EXPEDITION</span><span>|</span><span>MEDIA ROOM</span><span>|</span><span>SPONSORS</span><span>|</span><span>TANMO TRACKER</span><span>|</span><span>CONTESTS</span><span>|</span><span>STORE</span></nav>
  <div class="copy">COPYRIGHT © 2013 TANMO SKY LOOP · COPPER KESTRELS. ALL RIGHTS RESERVED.</div>
  <div class="social"><span aria-label="Social link"></span><span aria-label="Social link"></span><span aria-label="Video link"></span></div>
</footer>
</body>
</html>
```